Rultan Staffing Full Length Retractable Office Banner

I need a design for a full-length retractable banner and A-Frame Sign for each of my offices. I have included designs that have been incorporated into a poster and tri-fold as a sample. I would like to see a colorful eyecatching banner that focuses on people. Would like to see some diversity with men and woman and different races.
Rultan Staffing is a light industrial staffing firm. www.RultanStaffing.example

Target Market(s)

Job seekers looking for employment

Industry/Entity Type

Staffing / Recruiting

Font styles to use
Other font styles liked:
• Professional yet fun

Requirements
Must have
• Eye catching design with young hip vibe.
Nice to have
• primary colors with light industrial type jobs

```html
<!DOCTYPE html>
<html lang="en">
<head>
<meta charset="utf-8">
<title>Rultan Staffing Retractable Banner</title>
<link href="https://fonts.googleapis.com/css2?family=Montserrat:wght@400;700;800;900&display=swap" rel="stylesheet">
<style>
  :root {
    --stage: #ecebe8;
    --paper: #ffffff;
    --red: #e3261f;
    --green: #0d7a3e;
    --yellow: #e6c312;
    --navy: #25256a;
    --gray: #7d7d7d;
    --photo-top: #f3e7ec;
    --photo-mid: #b7c6d6;
    --photo-low: #6d7f99;
  }
  * { margin: 0; padding: 0; box-sizing: border-box; }
  html, body {
    width: 1200px; height: 900px; overflow: hidden;
    background: var(--stage);
    font-family: "Montserrat", Arial, sans-serif;
  }
  .banner {
    position: absolute; left: 410px; top: 10px;
    width: 380px; height: 880px;
    background: var(--paper);
    overflow: hidden;
    box-shadow: 0 2px 10px rgba(0,0,0,0.12);
  }
  .brand {
    position: absolute; top: 48px; left: 0; width: 100%;
    text-align: center;
    font-size: 34px; font-weight: 700; color: var(--navy);
    letter-spacing: -0.5px;
  }
  .hero-photo {
    position: absolute; top: 120px; left: 0; width: 100%; height: 390px;
    background:
      linear-gradient(180deg, rgba(255,255,255,0) 55%, var(--paper) 100%),
      linear-gradient(180deg, var(--photo-top) 0%, var(--photo-mid) 45%, var(--photo-low) 80%);
  }
  .headline { position: absolute; left: 0; width: 100%; text-align: center; line-height: 1; }
  .headline.connecting { top: 506px; font-size: 38px; font-weight: 800; color: var(--red); }
  .people-band {
    position: absolute; top: 545px; left: 15px; width: 353px; height: 45px;
    background: var(--green);
    color: var(--paper); font-size: 41px; font-weight: 800;
    text-align: center; line-height: 47px; letter-spacing: 0.5px;
  }
  .band-shadow {
    position: absolute; top: 594px; left: 60px; width: 262px; height: 3px;
    border-radius: 50%;
    background: linear-gradient(90deg, transparent, #777, transparent);
  }
  .headline.with { top: 609px; font-size: 34px; font-weight: 800; color: var(--gray); }
  .headline.great { top: 648px; font-size: 68px; font-weight: 900; color: var(--yellow); letter-spacing: 1px; }
  .headline.organizations { top: 708px; font-size: 36px; font-weight: 800; color: var(--navy); }
  .divider {
    position: absolute; top: 753px; left: 123px; width: 126px; height: 3px;
    background: var(--navy);
  }
  .headline.cta { top: 768px; font-size: 25px; font-weight: 800; color: var(--red); }
  .footer-wave { position: absolute; left: 0; top: 820px; width: 380px; height: 60px; }
  .website {
    position: absolute; left: 0; width: 100%; top: 850px;
    text-align: center; color: var(--paper);
    font-size: 17px; font-weight: 700; letter-spacing: 0.3px;
  }
</style>
</head>
<body>
  <main class="banner">
    <div class="brand">Rultan Staffing</div>
    <div class="hero-photo" role="img" aria-label="Photo of three young, diverse job seekers looking at a tablet and a phone together"></div>

    <div class="headline connecting">CONNECTING</div>
    <div class="people-band">GREAT PEOPLE</div>
    <div class="band-shadow"></div>
    <div class="headline with">WITH</div>
    <div class="headline great">GREAT</div>
    <div class="headline organizations">ORGANIZATIONS</div>
    <div class="divider"></div>
    <div class="headline cta">CALL TO ACTION</div>

    <svg class="footer-wave" viewBox="0 0 380 60" aria-hidden="true">
      <path d="M0 38 C 80 40, 130 4, 190 4 C 250 4, 300 34, 380 26 L380 60 L0 60 Z" fill="var(--navy)"/>
    </svg>
    <div class="website">www.RultanStaffing.example</div>
  </main>
</body>
</html>
```